We need a redesign of our current website: www.halvenridgegroup.com. Halvenridge Group is a fully integrated hospitality development, management, and investment firm. We strive for leadership in each of our segments by building quality assets, exacting high standards of customer service, and focusing on returns for our investors and partners.

It is our mission to provide our guests an exceptional lodging experience; our clients an unsurpassed level of management in their properties; and create positive returns for our investors and partners. We achieve our mission via a company culture of transparency, ownership of our actions, and accountability for our results.

Target Market(s)

hotel owners, hotel developers, hotel investors, bankers

Industry/Entity Type

Hospitality

Requirements
Must have
• Our logo has to be there along with the quote and the ability to convey the following quote off of our current website: "Halvenridge was founded on the principles of integrity, honesty, loyalty, and trust. These convictions embody our company at every level, and show in every action."

```html
<!DOCTYPE html>
<html lang="en">
<head>
<meta charset="utf-8">
<title>Halvenridge Group</title>
<link href="https://fonts.googleapis.com/css2?family=Open+Sans:ital,wght@0,400;0,600;0,700;1,400;1,600&display=swap" rel="stylesheet">
<style>
:root{
  --page:#f1f1f1;
  --orange:#d68a12;
  --orange-dark:#b86f00;
  --ink:#111;
  --text:#222;
  --card:#fafafa;
  --border:#dedede;
  --footer:#000;
  --footer-text:#fff;
}
*{margin:0;padding:0;box-sizing:border-box}
html,body{width:813px;height:1200px;overflow:hidden}
body{background:var(--page);font-family:"Open Sans",Arial,sans-serif;color:var(--text);position:relative}
.abs{position:absolute}

.site-header{left:75px;top:0;width:663px;height:90px;background:linear-gradient(#ededed,#dcdcdc)}
.brand{left:18px;top:20px;display:flex;align-items:center;gap:10px}
.brand-dot{width:46px;height:46px;border-radius:50%;background:var(--orange)}
.brand-name{font-size:20px;font-weight:600;color:var(--orange);letter-spacing:1px;line-height:1.1;white-space:nowrap}
.main-nav{left:0;top:0;width:663px;height:90px;font-size:9.5px;font-weight:600}
.main-nav a{position:absolute;top:37px;height:19px;line-height:19px;color:var(--ink);text-decoration:none;white-space:nowrap}
.main-nav a.active{background:linear-gradient(#555,#222);color:#fff;border-radius:2px;padding:0 9px}

.hero{left:75px;top:91px;width:663px;height:366px;background:#888;padding:5px;box-shadow:0 6px 8px rgba(0,0,0,.15)}
.hero-photo{width:653px;height:355px;background:linear-gradient(180deg,#2d2d5a 0%,#6a3a2a 30%,#c47a3a 55%,#2a6a5a 75%,#36c6d6 100%);position:relative}
.hero-caption{left:0;top:220px;width:272px;height:135px;background:linear-gradient(90deg,var(--orange-dark),var(--orange));color:#fff;padding:18px 0 0 28px;font-weight:600;font-size:19px;line-height:1.15}
.hero-caption b{font-size:25px;font-weight:700}
.slider-dots{left:32px;top:109px;display:flex;gap:4px;align-items:center}
.slider-dots span{width:7px;height:7px;border-radius:50%;background:#ddd}
.slider-dots .arrow{width:10px;height:10px;background:#111}
.slider-dots .on{background:#444}

.motto{left:90px;top:480px;width:408px;height:206px;background:linear-gradient(#fff,#e6e6e6);border:1px solid var(--border);border-radius:18px 18px 50% 50%/18px 18px 26px 26px;padding:18px 20px 0 20px;box-shadow:0 4px 6px rgba(0,0,0,.08)}
.section-title{font-size:16px;font-weight:700;letter-spacing:1px;color:var(--ink);white-space:nowrap}
.section-title em{font-style:normal;color:var(--orange)}
.motto blockquote{margin-top:16px;font-style:italic;font-size:14px;line-height:1.3;text-align:justify;color:#333}
.motto cite{display:block;text-align:right;margin:18px 8px 0 0;font-style:italic;font-size:14px;font-weight:600;color:#333}
.motto cite b{color:var(--orange-dark);margin-right:8px}

.recent{left:526px;top:481px;width:191px;height:205px;background:var(--card);border:1px solid var(--border);padding:5px 10px}
.recent .photo{margin-top:10px;width:163px;height:122px;border:2px solid #222;background:linear-gradient(#b87a3a,#e0b070 50%,#8a5a30)}
.recent p{margin-top:11px;font-size:9.5px;font-weight:700;color:var(--ink);white-space:nowrap}

.service{top:701px;width:192px;height:285px;background:var(--card);border:1px solid var(--border);padding:5px 10px}
.service .photo{margin-top:8px;width:163px;height:122px;border:2px solid #222}
.service p{margin-top:12px;font-size:8.4px;line-height:13.5px;text-align:justify;color:#222;width:176px}
.btn{display:inline-block;margin-top:13px;font-size:8px;font-weight:600;color:#fff;background:var(--orange-dark);border:1px solid #6b4400;padding:4px 8px}
.photo-resort{background:linear-gradient(#2d2d5a,#c47a3a 55%,#36c6d6)}
.photo-hall{background:linear-gradient(#b87a3a,#e0b070 50%,#8a5a30)}
.photo-growth{background:linear-gradient(#fff,#e9f3f8 60%,#4aa0d8)}

.site-footer{left:0;top:1017px;width:813px;height:183px;background:var(--footer);color:var(--footer-text)}
.footer-col h4{font-size:11px;font-weight:700;color:var(--orange);margin-bottom:12px}
.footer-col li{list-style:none;font-size:7.5px;line-height:17px;white-space:nowrap}
.footer-brand{left:376px;top:14px;display:flex;align-items:center;gap:8px}
.footer-brand .brand-dot{width:32px;height:32px;background:#777}
.footer-brand .brand-name{font-size:12px;color:#fff;letter-spacing:1.5px;line-height:1.15}
.address{left:423px;top:53px;font-size:7.5px;line-height:16px;white-space:nowrap}
.address b{font-weight:700}
.address .hl{color:var(--orange);font-weight:700;font-size:9px}
.newsletter{left:545px;top:13px;width:162px;height:90px;background:#1c1c1c;border-radius:3px;padding:6px 8px}
.newsletter h5{font-size:9px;font-weight:600;margin-bottom:6px}
.newsletter .field{height:14px;background:#fff;color:#333;font-size:7px;padding:2px 5px;margin-bottom:4px}
.newsletter .subscribe{position:absolute;right:18px;top:64px;background:var(--orange);color:#fff;font-size:9px;font-weight:600;padding:3px 8px;border-radius:2px}
.social{left:551px;top:117px;display:flex;gap:9px}
.social span{width:17px;height:17px;border-radius:50%;background:#8a8a8a}
.copyright{left:0;top:166px;width:813px;height:17px;background:#141414;font-size:6px;text-align:center;line-height:17px}
</style>
</head>
<body>

<header class="site-header abs">
  <div class="brand abs"><span class="brand-dot"></span><span class="brand-name">HALVENRIDGE<br>GROUP</span></div>
  <nav class="main-nav abs">
    <a class="active" href="#" style="left:287px">HOME</a>
    <a href="#" style="left:350px">ABOUT US</a>
    <a href="#" style="left:418px">SERVICES</a>
    <a href="#" style="left:481px">PROJECTS</a>
    <a href="#" style="left:543px">TEAM</a>
    <a href="#" style="left:588px">CONTACT</a>
  </nav>
</header>

<section class="hero abs">
  <div class="hero-photo" role="img" aria-label="Resort hotel at dusk with lit balconies, palm trees and a glowing pool">
    <div class="hero-caption abs">We Strive for<br><b>Leadership</b> in each<br>of our <b>Segments.</b>
      <div class="slider-dots abs"><span class="arrow"></span><span class="on"></span><span></span><span></span><span></span><span class="arrow"></span></div>
    </div>
  </div>
</section>

<section class="motto abs">
  <h2 class="section-title">OUR <em>MOTTO</em></h2>
  <blockquote>"Halvenridge was founded on the principles of integrity, honesty, loyalty, and trust. These convictions embody our company at every level, and show in every action."</blockquote>
  <cite><b>Devan Marlow</b>( President and CEO )</cite>
</section>

<aside class="recent abs">
  <h2 class="section-title">RECENT <em>PROJECTS</em></h2>
  <div class="photo" role="img" aria-label="Hotel banquet hall with set tables and warm ceiling lights"></div>
  <p>MEADOWBROOK INN &amp; SUITES</p>
</aside>

<article class="service abs" style="left:89px">
  <h2 class="section-title">DEVELOPMENT</h2>
  <div class="photo photo-resort" role="img" aria-label="Resort hotel with pool at night"></div>
  <p>When evaluating sites for purchase and hotel development, our experienced team conducts the full array of feasibility studies and market analyses.moving the project forward.</p>
  <span class="btn">READ MORE</span>
</article>
<article class="service abs" style="left:307px">
  <h2 class="section-title">MANAGEMENT</h2>
  <div class="photo photo-hall" role="img" aria-label="Hotel dining hall interior"></div>
  <p>When evaluating sites for purchase and hotel development, our experienced team conducts the full array of feasibility studies and market analyses.moving the project forward.</p>
  <span class="btn">READ MORE</span>
</article>
<article class="service abs" style="left:526px">
  <h2 class="section-title">INVESTMENT</h2>
  <div class="photo photo-growth" role="img" aria-label="Business silhouettes beside a rising growth arrow"></div>
  <p>When evaluating sites for purchase and hotel development, our experienced team conducts the full array of feasibility studies and market analyses.moving the project forward.</p>
  <span class="btn">READ MORE</span>
</article>

<footer class="site-footer abs">
  <div class="footer-col abs" style="left:88px;top:26px">
    <h4>OUR SERVICES</h4>
    <ul><li>Hospitality Development</li><li>hospitality Mangement</li><li>Building Quality Assets</li><li>Investing Firm</li></ul>
  </div>
  <div class="footer-col abs" style="left:199px;top:22px">
    <h4>OUR PROJECTS</h4>
    <ul><li>Meadowbrook Inn &amp; Suites - Cincinnati, OH</li><li>Harborline Express &amp; Suites - Eastgate Commons</li><li>Cedarwick Suites - Little Rock, AR</li><li>Stonepath Inn - Mason, OH</li><li>Wayfarer Lodge - Florence, KY</li><li>Sunrest Inn &amp; Suites - Castle Rock, CO</li></ul>
  </div>
  <div class="footer-brand abs"><span class="brand-dot"></span><span class="brand-name">HALVENRIDGE<br>GROUP</span></div>
  <div class="address abs">
    4180 Larkfield Ave. #212<br>Brookmere, OH 45102<br>
    <b>Office:</b> <span class="hl">555-014-2286</span><br>
    <b>Fax:</b> <span class="hl">555-017-3390</span><br>
    <span style="color:var(--orange)">info@halvenridgegroup.com</span>
  </div>
  <form class="newsletter abs">
    <h5>Newsletter SignUp</h5>
    <div class="field">Name</div>
    <div class="field">Email Address</div>
    <span class="subscribe">Subscribe</span>
  </form>
  <div class="social abs" aria-label="Social links"><span></span><span></span><span></span><span></span></div>
  <div class="copyright abs">Copyrights Reserved 2012 @ Halvenridge Group</div>
</footer>

</body>
</html>
```